Coastline Premier Retreats Business Card Design

Design a business card for Coastline Premier Retreats. Look at the website for colors and reference. Card should have logo, name, title, office number, mobile number, email, URL and a tagline like, "Luxury Hotel & Resort Email Marketing" (This might change).

https://www.coastlinepremierretreats.example

The rest I will leave up to your imagination.

Contact Information for Business Card

Logo, name, title, office number, mobile number, email, URL and a tagline like, "Luxury Hotel & Resort Email Marketing" (This might change).

```html
<!DOCTYPE html>
<html lang="en">
<head>
<meta charset="utf-8">
<title>Coastline Premier Retreats – Business Card</title>
<link rel="stylesheet" href="https://fonts.googleapis.com/css2?family=Montserrat:wght@700&family=Lato:wght@400;700&family=Dancing+Script:wght@600&display=swap">
<style>
  :root {
    --bg: #2c2c2c;
    --card: #1f1f1f;
    --orange: #f07a14;
    --white: #f2f2f2;
    --grey: #bdbdbd;
    --silver: #d9d9d9;
  }
  * { margin: 0; padding: 0; box-sizing: border-box; }
  html, body { width: 1200px; height: 689px; overflow: hidden; background: var(--bg); }
  .canvas {
    width: 1200px; height: 689px; position: relative;
    display: flex; align-items: center; justify-content: center; gap: 40px;
  }
  .card {
    width: 540px; height: 310px; background: var(--card);
    border-radius: 18px; position: relative;
    box-shadow: 0 18px 40px rgba(0,0,0,.45);
  }
  /* front */
  .card--front { display: flex; flex-direction: column; align-items: center; justify-content: center; }
  .front-brand {
    display: flex; align-items: center; gap: 14px;
  }
  .brand-square { width: 18px; height: 18px; background: var(--silver); }
  .front-brand__name {
    font-family: "Montserrat", sans-serif; font-weight: 700;
    font-size: 26px; letter-spacing: 2px; color: var(--silver); text-transform: uppercase;
  }
  .tagline {
    margin-top: 42px; font-family: "Dancing Script", cursive; font-weight: 600;
    font-size: 26px; color: var(--orange);
  }
  /* back */
  .back-brand {
    position: absolute; top: 52px; right: 34px;
    display: flex; align-items: center; gap: 10px;
  }
  .back-brand .brand-square { width: 12px; height: 12px; background: var(--orange); }
  .back-brand__name {
    font-family: "Montserrat", sans-serif; font-weight: 700; font-size: 15px;
    letter-spacing: 1.5px; color: var(--white); text-transform: uppercase;
  }
  .divider {
    position: absolute; left: 34px; right: 34px; top: 155px;
    height: 1px; background: var(--orange);
  }
  .person { position: absolute; left: 34px; top: 92px; }
  .person__name {
    font-family: "Lato", sans-serif; font-weight: 700; font-size: 30px;
    color: var(--orange); text-transform: uppercase; line-height: 1;
  }
  .person__title {
    font-family: "Lato", sans-serif; font-size: 15px; color: var(--grey); margin-top: 6px;
  }
  .contact {
    position: absolute; left: 34px; top: 172px; list-style: none;
    font-family: "Lato", sans-serif; font-size: 13.5px; color: var(--white);
  }
  .contact li { display: flex; align-items: center; gap: 10px; height: 24px; }
  .contact svg { width: 13px; height: 13px; fill: var(--orange); flex: none; }
  .address {
    position: absolute; right: 34px; top: 172px; text-align: right;
    font-family: "Lato", sans-serif; font-size: 13.5px; line-height: 24px; color: var(--white);
    font-style: normal;
  }
</style>
</head>
<body>
<main class="canvas">
  <section class="card card--front">
    <div class="front-brand">
      <span class="brand-square"></span>
      <span class="front-brand__name">Coastline Premier Retreats</span>
    </div>
    <p class="tagline">Luxury Hotel &amp; Resort Email Marketing</p>
  </section>

  <section class="card card--back">
    <div class="back-brand">
      <span class="brand-square"></span>
      <span class="back-brand__name">Coastline Premier Retreats</span>
    </div>
    <div class="person">
      <h1 class="person__name">Daniel Hartley</h1>
      <p class="person__title">Founder &amp; CEO</p>
    </div>
    <div class="divider"></div>
    <ul class="contact">
      <li><svg viewBox="0 0 24 24"><path d="M6.6 10.8a15.1 15.1 0 0 0 6.6 6.6l2.2-2.2a1 1 0 0 1 1-.25 11.4 11.4 0 0 0 3.6.57 1 1 0 0 1 1 1V20a1 1 0 0 1-1 1A17 17 0 0 1 3 4a1 1 0 0 1 1-1h3.5a1 1 0 0 1 1 1c0 1.25.2 2.45.57 3.57a1 1 0 0 1-.25 1z"/></svg>(555) 014-2870</li>
      <li><svg viewBox="0 0 24 24"><path d="M7 1h10a2 2 0 0 1 2 2v18a2 2 0 0 1-2 2H7a2 2 0 0 1-2-2V3a2 2 0 0 1 2-2zm0 3v14h10V4zm5 15.5a1.2 1.2 0 1 0 0 2.4 1.2 1.2 0 0 0 0-2.4z"/></svg>(555) 014-2871</li>
      <li><svg viewBox="0 0 24 24"><path d="M2 5h20v14H2zm2 2v.5l8 5 8-5V7zm0 2.9V17h16V9.9l-8 5z"/></svg>info@coastlinepremierretreats.example</li>
      <li><svg viewBox="0 0 24 24"><path d="M12 2a10 10 0 1 0 0 20 10 10 0 0 0 0-20zm6.9 6h-3a15.6 15.6 0 0 0-1.4-3.6A8 8 0 0 1 18.9 8zM12 4a14 14 0 0 1 1.9 4h-3.8A14 14 0 0 1 12 4zM4.3 14a8 8 0 0 1 0-4h3.4a16 16 0 0 0 0 4zm.8 2h3a15.6 15.6 0 0 0 1.4 3.6A8 8 0 0 1 5.1 16zm3-8h-3a8 8 0 0 1 4.4-3.6A15.6 15.6 0 0 0 8.1 8zM12 20a14 14 0 0 1-1.9-4h3.8A14 14 0 0 1 12 20zm2.3-6H9.7a14.7 14.7 0 0 1 0-4h4.6a14.7 14.7 0 0 1 0 4zm.2 5.6a15.6 15.6 0 0 0 1.4-3.6h3a8 8 0 0 1-4.4 3.6zm1.8-5.6a16 16 0 0 0 0-4h3.4a8 8 0 0 1 0 4z"/></svg>coastlinepremierretreats.example</li>
    </ul>
    <address class="address">
      Coastline Premier Retreats<br>
      4470 Harbor View Lane, Ste 12<br>
      Mystic, CT 06355
    </address>
  </section>
</main>
</body>
</html>
```